Book Cover with this title and sub title
Where Auntie Found Her Quiet Orchard
The little book to be smart with your money and help the environment.
Walter P. Brunk Ph. D.
Ellen R. Brunk
Picture below would be on the entire front cover. Words somehow incorporated for easy reading.

```html
<!DOCTYPE html>
<html lang="en">
<head>
<meta charset="utf-8">
<title>Where Auntie Found Her Quiet Orchard</title>
<link rel="stylesheet" href="https://fonts.googleapis.com/css2?family=Cinzel:wght@400;500&family=Bebas+Neue&display=swap">
<style>
  :root {
    --cover-orange: #f7a000;
    --cover-deep: #e07a00;
    --cover-yellow: #ffd21a;
    --cover-burnt: #b86200;
    --title-white: #ffffff;
    --title-brown: #7a4a1c;
    --subtitle-purple: #4d3f78;
    --rule-white: #fff6d8;
  }
  html, body {
    margin: 0;
    padding: 0;
    overflow: hidden;
    background: #ffffff;
  }
  .cover {
    position: relative;
    width: 933px;
    height: 1200px;
    overflow: hidden;
    background: var(--cover-orange);
  }
  .cover-art {
    position: absolute;
    inset: 0;
    background:
      radial-gradient(ellipse 55% 30% at 62% 80%, rgba(255,225,40,0.95) 0%, rgba(255,200,20,0.6) 45%, rgba(255,190,0,0) 80%),
      radial-gradient(ellipse 60% 40% at 80% 55%, rgba(255,215,60,0.55) 0%, rgba(255,215,60,0) 70%),
      radial-gradient(ellipse 50% 40% at 10% 60%, rgba(215,110,0,0.45) 0%, rgba(215,110,0,0) 70%),
      linear-gradient(180deg, var(--cover-orange) 0%, #ffab0a 35%, #ffc013 60%, var(--cover-deep) 88%, var(--cover-burnt) 100%);
  }
  .title-block {
    position: absolute;
    left: 0;
    right: 0;
    top: 196px;
    margin: 0;
    text-align: center;
    font-family: "Cinzel", serif;
  }
  .title-line {
    margin: 0;
    color: var(--title-white);
    font-weight: 400;
    text-shadow: 2px 4px 6px rgba(120, 60, 0, 0.45);
    line-height: 1;
  }
  .title-top {
    font-size: 60px;
    letter-spacing: -1px;
  }
  .title-middle {
    margin-top: 14px;
    font-size: 29px;
    color: var(--title-brown);
    letter-spacing: 10px;
    text-shadow: none;
  }
  .title-main {
    margin-top: 14px;
    font-size: 120px;
    letter-spacing: 12px;
  }
  .subtitle {
    position: absolute;
    left: 0;
    right: 0;
    top: 452px;
    margin: 0;
    text-align: center;
    font-family: "Bebas Neue", sans-serif;
    color: var(--subtitle-purple);
    font-size: 40px;
    line-height: 44px;
    letter-spacing: 0.3px;
  }
  .subtitle-line {
    display: block;
  }
  .subtitle-rule {
    position: absolute;
    top: 516px;
    width: 79px;
    height: 3px;
    background: var(--rule-white);
  }
  .rule-left { left: 169px; }
  .rule-right { left: 684px; }
  .authors {
    position: absolute;
    left: 0;
    right: 0;
    top: 1030px;
    margin: 0;
    text-align: center;
    font-family: "Cinzel", serif;
    color: var(--title-white);
    font-size: 60px;
    line-height: 68px;
    text-shadow: 1px 2px 4px rgba(110, 50, 0, 0.35);
  }
  .author-name {
    display: block;
  }
</style>
</head>
<body>
  <main class="cover">
    <div class="cover-art" role="img" aria-label="Full-cover close-up photograph of a honeybee gathering pollen inside a bright yellow flower against a soft orange background"></div>

    <header class="title-block">
      <h1 class="title-line title-top">WHERE AUNTIE FOUND</h1>
      <p class="title-line title-middle">HER QUIET</p>
      <p class="title-line title-main">ORCHARD</p>
    </header>

    <p class="subtitle">
      <span class="subtitle-line">The little book to be smart with your money</span>
      <span class="subtitle-line">and help the environment.</span>
    </p>
    <span class="subtitle-rule rule-left"></span>
    <span class="subtitle-rule rule-right"></span>

    <footer class="authors">
      <span class="author-name">Walter P. Brunk Ph. D.</span>
      <span class="author-name">Ellen R. Brunk</span>
    </footer>
  </main>
</body>
</html>
```